Tech business card design

We need an amazing business card design for our new business 'Pexla' a marketing tech startup based in Sydney, Australia. We provide an online marketplace for businesses to search and buy advertising media, connect with service providers and learn more about marketing. We wish to communicate 'cool tech', reliability and professionalism and design based around our logo.

Target Market(s)

Business Owners

Contact Information for Business Card

Name
Position
Email Address
Website
Phone Number

Font styles to use
Other font styles liked:
• Avenir & Avenir Next

Colors

Designer to choose colors to be used in the design.

```html
<!DOCTYPE html>
<html lang="en">
<head>
<meta charset="utf-8">
<title>Pexla Business Card</title>
<link rel="stylesheet" href="https://fonts.googleapis.com/css2?family=Nunito+Sans:wght@400;600;800&display=swap">
<style>
  :root {
    --backdrop: #efe7e7;
    --paper: #fbfbfa;
    --navy: #2f3160;
    --navy-deep: #272953;
    --teal: #5fb0bd;
    --teal-soft: #8fc6cf;
    --ink: #4a4c5e;
    --rule: #6a6c7c;
    --photo-a: #8d93a8;
    --photo-b: #4a4f78;
  }
  * { box-sizing: border-box; margin: 0; padding: 0; }
  html, body { width: 1200px; height: 858px; overflow: hidden; }
  body {
    background: var(--backdrop);
    font-family: "Nunito Sans", Arial, sans-serif;
    position: relative;
  }
  .card {
    position: absolute;
    width: 500px;
    height: 286px;
    top: 286px;
    box-shadow: 0 10px 24px rgba(60, 50, 60, 0.14);
    overflow: hidden;
  }
  .card--front { left: 640px; background: var(--paper); }
  .card--back { left: 60px; background: var(--navy); }

  /* Front */
  .front-wordmark {
    position: absolute;
    left: 118px;
    top: 34px;
    font-size: 64px;
    font-weight: 800;
    letter-spacing: -2px;
    color: var(--navy);
    line-height: 1;
  }
  .contact-list {
    position: absolute;
    left: 64px;
    top: 126px;
    list-style: none;
  }
  .contact-list li {
    display: flex;
    align-items: center;
    gap: 9px;
    font-size: 13px;
    color: var(--ink);
    height: 18px;
  }
  .contact-list svg { width: 11px; height: 11px; flex: none; }
  .front-rule {
    position: absolute;
    left: 64px;
    right: 52px;
    top: 190px;
    border-top: 1px solid var(--rule);
  }
  .name-block {
    position: absolute;
    right: 52px;
    top: 200px;
    width: 150px;
  }
  .person-name {
    font-size: 19px;
    font-weight: 600;
    color: var(--navy);
    letter-spacing: 0.5px;
    line-height: 1.1;
  }
  .person-name .surname { color: var(--teal); }
  .person-role {
    margin-top: 3px;
    padding: 3px 8px;
    font-size: 12px;
    color: #fff;
    background: linear-gradient(90deg, var(--navy) 0%, var(--teal) 100%);
  }
  .edge-band {
    position: absolute;
    left: 0; right: 0; bottom: 0;
    height: 7px;
    background: linear-gradient(90deg, var(--navy) 0%, var(--teal) 100%);
  }

  /* Back */
  .back-photo { position: absolute; inset: 0; width: 100%; height: 100%; }
  .back-wordmark {
    position: absolute;
    left: 268px;
    top: 176px;
    font-size: 64px;
    font-weight: 800;
    letter-spacing: -2px;
    color: #fff;
    line-height: 1;
  }
  .back-website {
    position: absolute;
    left: 270px;
    top: 244px;
    font-size: 12px;
    color: var(--teal-soft);
    letter-spacing: 0.3px;
  }
</style>
</head>
<body>
  <section class="card card--back" aria-label="Card back">
    <svg class="back-photo" viewBox="0 0 500 286" role="img" aria-label="Photo of a hand using a tablet with marketing charts">
      <defs>
        <linearGradient id="photoTone" x1="0" y1="0" x2="1" y2="1">
          <stop offset="0" stop-color="var(--photo-a)"/>
          <stop offset="1" stop-color="var(--photo-b)"/>
        </linearGradient>
      </defs>
      <path d="M0,0 L232,0 L290,152 Q298,176 272,172 L0,118 Z" fill="url(#photoTone)" stroke="#fff" stroke-width="6" stroke-linejoin="round"/>
    </svg>
    <div class="back-wordmark">pexla</div>
    <div class="back-website">www.pexlamedia.com.au</div>
  </section>

  <section class="card card--front" aria-label="Card front">
    <div class="front-wordmark">pexla</div>
    <ul class="contact-list">
      <li>
        <svg viewBox="0 0 12 12" aria-hidden="true"><rect x="3" y="0.5" width="6" height="11" rx="1" fill="none" stroke="var(--navy)" stroke-width="1.2"/><circle cx="6" cy="9.5" r="0.7" fill="var(--navy)"/></svg>
        +61 (0)400 555 019
      </li>
      <li>
        <svg viewBox="0 0 12 12" aria-hidden="true"><rect x="0.5" y="2" width="11" height="8" fill="var(--navy)"/><path d="M0.5,2 L6,7 L11.5,2" fill="none" stroke="#fff" stroke-width="1"/></svg>
        marcus@pexlamedia.com.au
      </li>
      <li>
        <svg viewBox="0 0 12 12" aria-hidden="true"><circle cx="6" cy="6" r="5.3" fill="none" stroke="var(--navy)" stroke-width="1.2"/><ellipse cx="6" cy="6" rx="2.3" ry="5.3" fill="none" stroke="var(--navy)" stroke-width="1"/><path d="M0.7,6 H11.3" stroke="var(--navy)" stroke-width="1"/></svg>
        www.pexlamedia.com.au
      </li>
    </ul>
    <div class="front-rule"></div>
    <div class="name-block">
      <p class="person-name">MARCUS <span class="surname">DALE</span></p>
      <p class="person-role">Founder | Director</p>
    </div>
    <div class="edge-band"></div>
  </section>
</body>
</html>
```